Flyer for the Radiant Harvest Worship Day

I am looking to create a flyer for a one day prayer retreat our church is organizing.
This flyer will be posted on social media, websites and will also be printed so it can be mailed to people.
I am looking for something professional, with good use of our logo and band colors (logo colors).
I am counting on the designer's skill, creativity, art and knowledge of media communication to produce a flyer that will effectively and quickly convey the message we are trying to spread.
CONTENT OF THE FLYER:
Event title: Radiant Harvest Worship Day
Date: Tuesday July 2nd, 2019
Time: 11:00AM - 7:00PM
Belmora Hotel, 4875 Wexley Avenue, Portland, Maine 04102 (Room: Juniper)
Event Key words to highlight what the event is about: Prayer, Sharing the Word, Panel discussion, prophecy, Impartation.
Key phrases:
A one day prayer retreat.
Jesus Chris is Lord
Contact info:
www.tolvex.org
Phone: 207 555 3184
Email: contact@brookhavenfold.org

```html
<!DOCTYPE html>
<html lang="en">
<head>
<meta charset="utf-8">
<title>Radiant Harvest Worship Day</title>
<link rel="stylesheet" href="https://fonts.googleapis.com/css2?family=Bebas+Neue&family=Roboto:wght@300&display=swap">
<style>
  :root {
    --page: #ffffff;
    --card: #383736;
    --ink: #ffffff;
    --cream: #f4f0b4;
    --title-pale: #e9e6b0;
    --gold-top: #f6d77a;
    --gold-bottom: #b9821f;
    --sky-glow: #f3f2c6;
    --sky-light: #c9c8a0;
    --sky-mid: #8c8b6c;
    --sky-dark: #4a4a40;
    --crowd: #2c2c2a;
  }
  * { margin: 0; padding: 0; box-sizing: border-box; }
  html, body {
    width: 883px; height: 1200px; overflow: hidden;
    background: var(--page);
  }
  .flyer {
    position: absolute; left: 54px; top: 51px;
    width: 775px; height: 1112px;
    background: var(--card);
    overflow: hidden;
    font-family: "Roboto", "Helvetica Neue", Arial, sans-serif;
    font-weight: 300;
    color: var(--ink);
  }
  .hero-photo {
    position: absolute; left: 0; top: 0; width: 100%; height: 560px;
    background:
      linear-gradient(180deg, transparent 0%, transparent 62%, var(--crowd) 86%, var(--card) 100%),
      radial-gradient(ellipse 34% 30% at 66% 22%, var(--sky-glow) 0%, rgba(243,242,198,0) 100%),
      radial-gradient(ellipse 30% 24% at 14% 34%, rgba(201,200,160,0.55) 0%, rgba(201,200,160,0) 100%),
      radial-gradient(ellipse 40% 35% at 92% 50%, rgba(201,200,160,0.5) 0%, rgba(201,200,160,0) 100%),
      radial-gradient(ellipse 30% 22% at 20% 6%, var(--sky-dark) 0%, rgba(74,74,64,0) 100%),
      linear-gradient(180deg, var(--sky-mid) 0%, #77765c 45%, #55554a 70%, var(--crowd) 100%);
  }
  .event-title {
    font-family: "Bebas Neue", "Oswald", sans-serif;
    font-weight: 400;
  }
  .event-title span {
    position: absolute; left: 0; width: 100%;
    text-align: center; line-height: 1; white-space: nowrap;
  }
  .event-title .title-top {
    top: 510px; font-size: 62px; letter-spacing: 1px;
    color: var(--title-pale);
  }
  .event-title .title-main {
    top: 564px; font-size: 80px; letter-spacing: 2px;
    background: linear-gradient(180deg, var(--gold-top) 0%, var(--gold-bottom) 100%);
    -webkit-background-clip: text; background-clip: text;
    color: transparent;
  }
  .event-details {
    position: absolute; left: 0; top: 700px; width: 100%;
    list-style: none; text-align: center;
    font-size: 31px; line-height: 45px; white-space: nowrap;
  }
  .event-details svg {
    width: 26px; height: 26px; vertical-align: -3px; margin-right: 6px;
    fill: none; stroke: var(--ink); stroke-width: 1.4;
  }
  .tagline {
    position: absolute; left: 0; top: 949px; width: 100%;
    text-align: center; font-size: 31px; line-height: 38px;
  }
  .motto {
    position: absolute; left: 0; top: 989px; width: 100%;
    display: flex; align-items: center; justify-content: center; gap: 12px;
    font-size: 47px; line-height: 56px; color: var(--cream); white-space: nowrap;
  }
  .motto .rule { width: 95px; height: 2px; background: var(--cream); }
</style>
</head>
<body>
  <main class="flyer">
    <div class="hero-photo" role="img" aria-label="Worshipper with raised arms before three crosses against a glowing cloudy sky, crowd of raised hands in silhouette"></div>

    <h1 class="event-title">
      <span class="title-top">Radiant Harvest</span>
      <span class="title-main">Worship Day</span>
    </h1>

    <ul class="event-details">
      <li><svg viewBox="0 0 24 24" aria-hidden="true"><rect x="3" y="5" width="18" height="16"/><line x1="3" y1="10" x2="21" y2="10"/><line x1="8" y1="3" x2="8" y2="7"/><line x1="16" y1="3" x2="16" y2="7"/><line x1="9" y1="10" x2="9" y2="21"/><line x1="15" y1="10" x2="15" y2="21"/><line x1="3" y1="15.5" x2="21" y2="15.5"/></svg>Date: Tuesday July 2nd, 2019</li>
      <li><svg viewBox="0 0 24 24" aria-hidden="true"><circle cx="12" cy="13" r="8"/><polyline points="12,8 12,13 15,15"/><line x1="5" y1="4" x2="8" y2="2.5"/><line x1="19" y1="4" x2="16" y2="2.5"/></svg>Time: 11:00AM - 7:00PM</li>
      <li><svg viewBox="0 0 24 24" aria-hidden="true"><path d="M12 21s-6-6.5-6-11a6 6 0 0 1 12 0c0 4.5-6 11-6 11z"/><circle cx="12" cy="10" r="2.3"/><ellipse cx="12" cy="21" rx="4" ry="1.2"/></svg>Belmora Hotel, 4875 Wexley Avenue,</li>
      <li>Portland, Maine 04102 (Room: Juniper)</li>
    </ul>

    <p class="tagline">A one day prayer retreat.</p>
    <p class="motto"><span class="rule"></span>Jesus Chris is Lord<span class="rule"></span></p>
  </main>
</body>
</html>
```